UX - Need some screens design for a Skill Assessment Application

I am building an app to carry out skill assessments. Depending on how the assessment is configured, it may have one or more parts
1. Question based assessment (Multiple Choice, True False, Fill in the blanks"
2. Endorsement by two colleagues - A screen that allows user to pick colleagues based on search and shows the status of pending requests
3. A written submission - a page that explains the format of the submission and a file upload
As each assessment can be configured with or without any of the steps, the assessment UI must be such that these areas get hidden/displayed based on configuration.
Colour codes to be used can be #0e78bb and #ffffff
There will also be a start screen (instructions) and an end screen (results)
Target Market(s)
Enterprise software
Number of Pages Required
4 page

```html
<!DOCTYPE html>
<html lang="en">
<head>
<meta charset="utf-8">
<title>Application Design Capabilities – Assessment</title>
<link href="https://fonts.googleapis.com/css2?family=Inter:wght@400;500;600;700&display=swap" rel="stylesheet">
<style>
  :root {
    --header-blue: #0a55a8;
    --brand-blue: #0e78bb;
    --link-blue: #1689c9;
    --deep-blue: #0b4f96;
    --white: #ffffff;
    --page-bg: #f5f6f8;
    --bar-bg: #f1f2f4;
    --line: #dcdfe3;
    --text-dark: #222428;
    --text-mid: #555a60;
    --text-soft: #6b7076;
    --chip-bg: #cfe9f6;
    --selected-bg: #e8f5fb;
    --ring-track: #dcdfe3;
  }
  * { box-sizing: border-box; margin: 0; padding: 0; }
  html, body { width: 1200px; height: 686px; overflow: hidden; }
  body {
    font-family: "Inter", Arial, sans-serif;
    background: var(--page-bg);
    color: var(--text-dark);
    position: relative;
  }

  /* Top navigation */
  .topbar {
    height: 43px;
    background: var(--header-blue);
    display: flex;
    align-items: center;
    padding: 0 57px;
    color: var(--white);
  }
  .brand { display: flex; align-items: center; gap: 9px; font-size: 14px; font-weight: 600; }
  .brand-dot { width: 20px; height: 20px; border-radius: 50%; background: var(--white); }
  .main-nav { margin-left: auto; display: flex; align-items: center; font-size: 12.5px; }
  .main-nav a { color: rgba(255,255,255,0.82); text-decoration: none; margin-left: 21px; }
  .main-nav a.is-active { color: var(--white); font-weight: 600; margin-left: 0; }
  .user-menu { display: flex; align-items: center; gap: 6px; margin-left: 62px; margin-right: -2px; }
  .avatar { width: 27px; height: 27px; border-radius: 50%; background: linear-gradient(135deg, #8a6a5c, #3a3b45); }

  /* Page header */
  .page-head { background: var(--white); height: 97px; position: relative; }
  .crumbs { position: absolute; left: 57px; top: 22px; display: flex; align-items: center; font-size: 11.5px; color: var(--text-mid); }
  .crumbs a { color: var(--link-blue); text-decoration: none; margin-left: 11px; }
  .crumbs .sep { margin: 0 7px; }
  .updated { position: absolute; right: 88px; top: 23px; font-size: 11.5px; color: var(--text-mid); }
  .updated b { font-weight: 500; color: var(--text-dark); }
  .title-row { position: absolute; left: 88px; top: 56px; display: flex; align-items: center; gap: 14px; }
  .title-row h1 { font-size: 21px; font-weight: 600; letter-spacing: -0.1px; }
  .btn {
    font-family: inherit; font-size: 11.5px; font-weight: 500;
    border-radius: 3px; height: 31px; display: inline-flex; align-items: center; justify-content: center;
  }
  .btn-outline { background: var(--white); border: 1px solid var(--brand-blue); color: var(--brand-blue); }
  .btn-solid { background: var(--brand-blue); border: 1px solid var(--brand-blue); color: var(--white); }
  .save-progress { position: absolute; right: 88px; top: 56px; width: 104px; }

  /* Info bar */
  .info-bar {
    height: 45px; background: var(--bar-bg);
    border-top: 1px solid var(--line); border-bottom: 1px solid var(--line);
    display: flex; align-items: center; padding: 0 88px; font-size: 10.3px; color: var(--text-dark);
  }
  .info-item { padding-right: 21px; margin-right: 21px; border-right: 1px solid var(--line); line-height: 14px; }
  .info-item:last-of-type { border-right: 0; }
  .info-item .value { color: var(--link-blue); }
  .info-item .muted { color: var(--text-soft); }
  .progress { margin-left: auto; display: flex; align-items: center; gap: 6px; font-size: 10.5px; color: var(--text-soft); }
  .progress b { color: var(--text-dark); font-weight: 600; }

  /* Question */
  .question { position: absolute; left: 367px; top: 218px; width: 468px; }
  .question-head { display: flex; align-items: baseline; font-size: 15px; margin-bottom: 24px; }
  .question-num { width: 50px; color: var(--text-soft); }
  .question-text { color: var(--text-dark); }
  .options { list-style: none; }
  .option {
    height: 68px; background: var(--white); border: 1px solid transparent; border-radius: 2px;
    box-shadow: 0 1px 4px rgba(0,0,0,0.07);
    display: flex; align-items: center; padding-left: 13px; margin-bottom: 7.5px;
    font-size: 12px; color: var(--text-mid);
  }
  .option-key {
    width: 31px; height: 28px; background: var(--chip-bg); color: var(--text-soft);
    display: flex; align-items: center; justify-content: center; font-size: 13px; margin-right: 21px;
  }
  .option.is-selected { background: var(--selected-bg); border-color: var(--deep-blue); color: var(--deep-blue); box-shadow: none; }

  .actions { border-top: 1px solid var(--line); margin-top: 20px; padding-top: 27px; display: flex; align-items: center; }
  .go-back { width: 72px; }
  .skip { margin-left: auto; margin-right: 25px; font-size: 11.5px; color: var(--text-mid); display: flex; align-items: center; gap: 5px; }
  .next { width: 53px; }
</style>
</head>
<body>
  <header class="topbar">
    <div class="brand"><span class="brand-dot"></span>Skillgrid</div>
    <nav class="main-nav">
      <a class="is-active" href="#">Assessments</a>
      <a href="#">Endorsement</a>
      <a href="#">Submissions</a>
      <a href="#">Results</a>
    </nav>
    <div class="user-menu">
      <div class="avatar" role="img" aria-label="User profile photo"></div>
      <svg width="10" height="7" viewBox="0 0 10 7"><path d="M1 1l4 4 4-4" fill="none" stroke="#fff" stroke-width="1.6"/></svg>
    </div>
  </header>

  <section class="page-head">
    <div class="crumbs">
      <svg width="19" height="19" viewBox="0 0 19 19"><circle cx="9.5" cy="9.5" r="8.5" fill="none" stroke="#0e78bb" stroke-width="1.6"/><path d="M13.5 9.5H6M9 6.3L5.8 9.5 9 12.7" fill="none" stroke="#0e78bb" stroke-width="1.6"/></svg>
      <a href="#">Assessment</a><span class="sep">/</span><span>Application Design Capabilities</span>
    </div>
    <div class="updated">Last Updated: <b>17/05/2024</b></div>
    <div class="title-row">
      <svg width="22" height="22" viewBox="0 0 22 22"><rect x="2" y="1.5" width="13" height="17" rx="1" fill="none" stroke="#555a60" stroke-width="1.5"/><path d="M5 6h7M5 9.5h5M5 13h3" stroke="#555a60" stroke-width="1.5"/><circle cx="15.5" cy="15.5" r="5" fill="#555a60"/><path d="M13.3 15.5l1.6 1.6 2.9-3" fill="none" stroke="#fff" stroke-width="1.4"/></svg>
      <h1>Application Design Capabilities</h1>
    </div>
    <button class="btn btn-outline save-progress">Save Progress</button>
  </section>

  <section class="info-bar">
    <div class="info-item">Assessment Date: <span class="value">September 23, 2024</span></div>
    <div class="info-item">Assessment Type: <span class="value">UI/UX Skill</span></div>
    <div class="info-item">Assessment Responses: <span class="muted">4 of 8 Responded / Closed: in next 4 month</span></div>
    <div class="progress">
      <svg width="32" height="32" viewBox="0 0 32 32"><circle cx="16" cy="16" r="13" fill="none" stroke="var(--ring-track)" stroke-width="4"/><circle cx="16" cy="16" r="13" fill="none" stroke="#1a9ad6" stroke-width="4" stroke-dasharray="51 82" transform="rotate(-90 16 16)"/></svg>
      <span><b>5</b> / 8</span>
    </div>
  </section>

  <main class="question">
    <div class="question-head">
      <span class="question-num">Q.5.</span>
      <span class="question-text">What’s your knowledge regarding User Interface?</span>
    </div>
    <ol class="options">
      <li class="option"><span class="option-key">1</span>Lorem ipsum dolor sit amet, consecteteur adispiscing elit.</li>
      <li class="option"><span class="option-key">2</span>Lorem ipsum dolor sit amet, consecteteur adispiscing elit.</li>
      <li class="option is-selected"><span class="option-key">3</span>Lorem ipsum dolor sit amet, consecteteur adispiscing elit.</li>
      <li class="option"><span class="option-key">4</span>Lorem ipsum dolor sit amet, consecteteur adispiscing elit.</li>
    </ol>
    <div class="actions">
      <button class="btn btn-outline go-back">Go Back</button>
      <span class="skip">Skip <svg width="6" height="9" viewBox="0 0 6 9"><path d="M1 1l3.5 3.5L1 8" fill="none" stroke="#555a60" stroke-width="1.5"/></svg></span>
      <button class="btn btn-solid next">Next</button>
    </div>
  </main>
</body>
</html>
```